Hardcore nerd needs to stand out in a sea of dull Defence business cards

Wombarra Devices is a new Australian consulting engineering company that turns research and theory into practical systems. No evangelistic fluff, just mathematics and physics into electronic and optical circuits for consumer products, scientific research or Defence applications.

We already have a recognised logo (provided) which is often dark blue/black on a light background but we're open to other combinations. (Us engineers tend to have limited aesthetic imagination :)

Some of our recent products have included:
* Instrumentation for electrical testing,
* Radar jammers,
* GPS antenna design,
* Satellite tracking systems,
* High power lasers

We're open to both single and double-sided designs - happy to be convinced either way.

P.S. Another group is working on the web page, so - alas - our web site is currently of no use for images/ideas...

Target Market(s)

Engineering managers,
Scientists

Contact Information for Business Card

Dr Colin Harte
R&D Engineer

colin@wombarradevices.com.au
0427 563 710

PO Box XXX (to be confirmed)
Kelsby ACT 2917
Australia

Font styles to use
Serif
Sans Serif

Colors

Designer to choose colors to be used in the design.

Requirements
Must have
• My contact details!
• I've had many (great) "bold and plain" designs submitted already, so feel free to be artistically creative :)
• Happy to take advice re fonts/colours/printability etc.
Nice to have
• I'm not sure if "lists" are more at home on a CV than a business card, but representative services include:
• Applied electromagnetics
• RF and high speed electronics
• Signal and image processing
• Electro-optical and laser systems
• Concept-to-prototype design services
• If you're considering double sided cards, then often measuring/alignment grids/rulers feature on the back of similar cards.
• e.g. https://www.veltranoptics.example/newgrouppage9.cfm?objectgroup_id=4183
• https://www.veltranoptics.example/newgrouppage9.cfm?objectgroup_ID=4185
• ..or even a "Smith chart" (google will return lots)
• Generic images to represent a capability might work - googling images associated with keyword for each of these areas might help:
• - "passive radar", "phased array", "fdtd", "vircator"
• RF and high speed electronic design
• - "smith chart", "microstrip circuits", "dimensioned drawing", "electronic schematic"
• - "dft", "iir filter"
• - "optical cavity". "laser energy level diagram"
• Background/watermarked images outlines/wireframes/schematics would probably look OK.
Should not have
• If a list of projects/services is provided, it is important not to make the client feel that this is "all" the company can do. Engineering design is a creative discipline (like graphics :)
• Please, no stock "military" snaps like planes, missiles, etc!

```html
<!DOCTYPE html>
<html lang="en">
<head>
<meta charset="utf-8">
<title>Wombarra Devices – Business Card</title>
<link rel="stylesheet" href="https://fonts.googleapis.com/css2?family=Roboto:wght@400;700&display=swap">
<style>
  :root {
    --navy: #0b2a6f;
    --navy-deep: #05205c;
    --navy-top: #0a2d70;
    --ink: #3a3a3a;
    --muted: #9a9a9a;
    --band-dark: #161616;
    --paper: #ffffff;
    --backdrop: #dcdcdc;
  }
  * { margin: 0; padding: 0; box-sizing: border-box; }
  html, body { width: 1200px; height: 1200px; overflow: hidden; }
  body {
    background: var(--backdrop);
    font-family: "Roboto", Arial, sans-serif;
    position: relative;
  }
  .card {
    position: absolute;
    left: 257px;
    width: 686px;
    height: 392px;
    overflow: hidden;
  }
  .card--front { top: 165px; background: var(--paper); }
  .card--back {
    top: 653px;
    background: linear-gradient(180deg, var(--navy-top) 0%, var(--navy-deep) 100%);
    color: #fff;
  }

  /* Front: brand */
  .brand {
    position: absolute;
    left: 62px;
    top: 158px;
    display: flex;
    align-items: center;
    gap: 12px;
  }
  .brand__mark {
    width: 70px; height: 70px;
    border-radius: 50%;
    background: var(--navy);
  }
  .brand__name {
    font-weight: 700;
    font-size: 25px;
    line-height: 27px;
    letter-spacing: 1px;
    color: var(--navy);
    text-transform: uppercase;
  }

  .divider {
    position: absolute;
    left: 333px; top: 113px;
    width: 1.5px; height: 166px;
    background: var(--navy);
  }

  /* Front: contact */
  .contact {
    position: absolute;
    left: 356px; top: 112px;
    color: var(--ink);
    font-size: 15.5px;
    line-height: 19.5px;
  }
  .contact__name {
    font-weight: 700;
    font-size: 23px;
    line-height: 26px;
    color: var(--navy);
  }
  .contact__role { color: var(--muted); margin-bottom: 6px; }
  .contact__address { margin-bottom: 9px; }
  .contact__line { display: flex; align-items: center; gap: 8px; }
  .contact__line svg { width: 13px; height: 13px; fill: var(--navy); flex: none; }
  .contact__line--email { font-size: 15px; }

  /* Front: band */
  .band {
    position: absolute;
    left: 0; top: 336px;
    width: 100%; height: 34px;
    background: linear-gradient(90deg, var(--navy) 0 573px, var(--band-dark) 573px 100%);
  }
  .band__url {
    position: absolute;
    left: 107px; top: 8px;
    font-size: 15px;
    letter-spacing: 3.6px;
    color: #fff;
  }
  .band__mark {
    position: absolute;
    left: 540px; top: -2px;
    width: 38px; height: 38px;
    border-radius: 50%;
    background: var(--paper);
    border: 3px solid var(--navy);
  }

  /* Back */
  .back__mark {
    position: absolute;
    left: 283px; top: 78px;
    width: 120px; height: 120px;
    border-radius: 50%;
    background: #fff;
  }
  .back__name {
    position: absolute;
    left: 0; width: 100%;
    top: 214px;
    text-align: center;
    font-weight: 700;
    font-size: 24px;
    letter-spacing: 2px;
    text-transform: uppercase;
  }
  .services {
    position: absolute;
    left: 0; width: 100%;
    top: 306px;
    text-align: center;
    font-size: 16.5px;
    line-height: 19.5px;
    list-style: none;
  }
</style>
</head>
<body>

<section class="card card--front" aria-label="Business card front">
  <div class="brand">
    <span class="brand__mark"></span>
    <span class="brand__name">Wombarra<br>Devices</span>
  </div>

  <div class="divider"></div>

  <div class="contact">
    <p class="contact__name">Dr Colin Harte</p>
    <p class="contact__role">R&amp;D Engineer</p>
    <p class="contact__address">PO Box 618<br>Kelsby ACT 2917<br>Australia</p>
    <p class="contact__line">
      <svg viewBox="0 0 24 24" aria-hidden="true"><path d="M6.6 10.8a15.1 15.1 0 0 0 6.6 6.6l2.2-2.2c.3-.3.7-.4 1-.2 1.1.4 2.3.6 3.6.6.6 0 1 .4 1 1V20c0 .6-.4 1-1 1A17 17 0 0 1 3 4c0-.6.4-1 1-1h3.5c.6 0 1 .4 1 1 0 1.3.2 2.5.6 3.6.1.3 0 .7-.2 1z"/></svg>
      0427 563 710
    </p>
    <p class="contact__line contact__line--email">
      <svg viewBox="0 0 24 24" aria-hidden="true"><path d="M2 5h20v14H2zm2 2v.4l8 5 8-5V7zm0 2.8V17h16V9.8l-8 5z"/></svg>
      colin@wombarradevices.com.au
    </p>
  </div>

  <div class="band">
    <span class="band__url">www.wombarradevices.com.au</span>
    <span class="band__mark"></span>
  </div>
</section>

<section class="card card--back" aria-label="Business card back">
  <span class="back__mark"></span>
  <p class="back__name">Wombarra Devices</p>
  <ul class="services">
    <li>Applied electromagnetics • RF &amp; high speed electronics</li>
    <li>Signal &amp; image processing • Electro-optical &amp; laser systems</li>
    <li>Concept-to-prototype design services</li>
  </ul>
</section>

</body>
</html>
```